Yacht, Boats, Watersports company needs a redesign of business card

Hello Designers!
We are a Boat dealership company that sells fun in the water, we sell boats, Yachts, Kayaks and also yacht WaterSport toys. We are looking to redesign our business cards in to something a little bit more sophisticated. in a way that we can make better use of our company colors. I'm attaching a zipped file containing the company 3 sets of company logo which one is an horizontal another one is a vertical and also a chromed 3d logo. Also is included two set of business cards that we use and also some designs that i think it's interesting. We use PMS 2026c Orange and PMS 7687C Blue. I would like to see at least two different options with the orange as accent and also using blue as an accent color. It's really important for the business cards to have a font option and size that is legible to most people. Our current website is wwww.coralpennant.com. Please visit if you want to have a better feeling of the Boat dealership
You can send Single sided or double side options. We are now using single sided but we may be open for a double side option if we really like the design.
Target Market(s)
Marine, boat sales, yacht sales, water toys sales/
Contact Information for Business Card
Name: Dale Whitcombe
Address: 212 North Fenwick Lane,
Harbor Cove, FL 33019
Phone: 954-731-8842
Fax: 954:731-8843
Cell: 954-382-1490
Email: dw@coralpennant.com
Website: coralpennant.com
Requirements
Must have
- the current information of the business card provided.
logo
use the PMS Colors
Nice to have
- a touch of elegance and sophistication but simple
Should not have
- should not have any typography that is hard to read, the card should be simple but yet sophisticated.

```html
<!DOCTYPE html>
<html lang="en">
<head>
<meta charset="utf-8">
<title>Coral Pennant Marine Center – Business Card</title>
<link rel="stylesheet" href="https://fonts.googleapis.com/css2?family=Poppins:wght@400;600&display=swap">
<style>
  :root {
    --backdrop: #2b2b2b;
    --brand-blue: #1f6fb2;
    --brand-orange: #ee8a26;
    --paper: #ffffff;
    --back-mark: #5cc8f0;
  }
  * { box-sizing: border-box; margin: 0; padding: 0; }
  html, body { width: 1125px; height: 1200px; overflow: hidden; }
  body {
    background: var(--backdrop);
    font-family: "Poppins", sans-serif;
    position: relative;
  }
  .card {
    position: absolute;
    left: 150px;
    width: 825px;
    height: 471px;
    overflow: hidden;
  }
  .card--front { top: 106px; background: var(--paper); }
  .card--back { top: 639px; background: var(--brand-blue); }

  .brand {
    position: absolute;
    left: 0; right: 0;
    text-align: center;
    font-weight: 600;
    line-height: 1.1;
  }
  .brand__dot {
    display: block;
    margin: 0 auto 26px;
    width: 96px; height: 96px;
    border-radius: 50%;
    border: 9px solid currentColor;
  }
  .brand__name { display: block; font-size: 28px; letter-spacing: 1px; }
  .brand__sub { display: block; font-size: 20px; letter-spacing: 1px; margin-top: 10px; }
  .card--front .brand { top: 60px; color: var(--brand-blue); }
  .card--back .brand { top: 122px; color: var(--back-mark); }

  .contact-band {
    position: absolute;
    left: 0; right: 0; bottom: 0;
    height: 156px;
    display: flex;
    gap: 2px;
    background: var(--paper);
    color: var(--paper);
  }
  .contact-band__person {
    width: 412px;
    background: var(--brand-blue);
    padding: 16px 0 0 44px;
  }
  .person__name { font-size: 25px; font-weight: 600; line-height: 1.3; margin-bottom: 4px; }
  .person__line { font-size: 18px; font-weight: 400; line-height: 23px; }
  .person__web { margin-top: 3px; }

  .contact-band__lines {
    flex: 1;
    background: var(--brand-orange);
    padding: 28px 46px 0 0;
    list-style: none;
    text-align: right;
  }
  .contact-line {
    font-size: 18px;
    line-height: 23.5px;
    display: flex;
    justify-content: flex-end;
    align-items: center;
    gap: 8px;
  }
  .contact-line svg { width: 15px; height: 15px; fill: var(--paper); flex: none; }
</style>
</head>
<body>

<section class="card card--front" aria-label="Business card front">
  <div class="brand">
    <span class="brand__dot"></span>
    <span class="brand__name">CORAL PENNANT</span>
    <span class="brand__sub">MARINE CENTER</span>
  </div>

  <div class="contact-band">
    <div class="contact-band__person">
      <p class="person__name">DALE WHITCOMBE</p>
      <p class="person__line">212 North Fenwick Lane</p>
      <p class="person__line">Harbor Cove, FL 33019</p>
      <p class="person__line person__web">www.CoralPennant.com</p>
    </div>
    <ul class="contact-band__lines">
      <li class="contact-line">954-731-8842
        <svg viewBox="0 0 24 24" aria-label="Phone"><path d="M6.6 10.8a15.1 15.1 0 0 0 6.6 6.6l2.2-2.2c.3-.3.7-.4 1-.2 1.1.4 2.3.6 3.6.6.6 0 1 .4 1 1V20c0 .6-.4 1-1 1A17 17 0 0 1 3 4c0-.6.4-1 1-1h3.5c.6 0 1 .4 1 1 0 1.3.2 2.5.6 3.6.1.3 0 .7-.2 1z"/></svg>
      </li>
      <li class="contact-line">954-382-1490
        <svg viewBox="0 0 24 24" aria-label="Mobile"><path d="M7 1h10a2 2 0 0 1 2 2v18a2 2 0 0 1-2 2H7a2 2 0 0 1-2-2V3a2 2 0 0 1 2-2zm0 3v14h10V4zm5 15.5a1 1 0 1 0 0 2 1 1 0 0 0 0-2z"/></svg>
      </li>
      <li class="contact-line">954-731-8843
        <svg viewBox="0 0 24 24" aria-label="Fax"><path d="M6 2h9l3 3v4H6zM3 10h18a1 1 0 0 1 1 1v8a1 1 0 0 1-1 1H3a1 1 0 0 1-1-1v-8a1 1 0 0 1 1-1zm3 4v2h12v-2z"/></svg>
      </li>
      <li class="contact-line">dw@coralpennant.com
        <svg viewBox="0 0 24 24" aria-label="Email"><path d="M2 5h20v2l-10 6L2 7zm0 4.3 10 6 10-6V19H2z"/></svg>
      </li>
    </ul>
  </div>
</section>

<section class="card card--back" aria-label="Business card back">
  <div class="brand">
    <span class="brand__dot"></span>
    <span class="brand__name">CORAL PENNANT</span>
    <span class="brand__sub">MARINE CENTER</span>
  </div>
</section>

</body>
</html>
```